NEW Modern Sleek Business Card for VR Language Startup

Our startup is using VR to lead the next wave of world language education. We need a two-sided business card that introduces the larger organization (Brightloom Language Inc) and our contact info on one side and shows the product, Glimwoorld, on the other side.

Side 1 (contact info)= Brightloom Logo and Contact info (name, title, phone, email)

Side 2 (product)= Glimworld logo, text, and website
Text= Culturally Immersive Language Learning Games
Website= www.glimworld-play.com

Target Market(s)

Education, Technology

Contact Information for Business Card

Contact info will be updated upon approval of the design. For now, put this as a placeholder.

Perry Dunmore
Founder & CEO
pdunmore@quillpost-mail.net
(555)-014-2286

Font styles to use
Other font styles liked:
• Gibson and Century Gothic are the brand fonts

Requirements
Nice to have
• I would love to see cohesion between the design and colors of the two logos. I have attached a few business card designs that I like, so you can get a feel for my preferred style.

```html
<!DOCTYPE html>
<html lang="en">
<head>
<meta charset="utf-8">
<title>Brightloom Language – Business Card</title>
<link rel="stylesheet" href="https://fonts.googleapis.com/css2?family=Montserrat:wght@700&family=Open+Sans:wght@400;700&family=Questrial&display=swap">
<style>
  :root {
    --stage: #262626;
    --card-dark: #1d1d1d;
    --card-light: #ffffff;
    --ink: #1a1a1a;
    --ink-soft: #3a3a3a;
    --paper-text: #ffffff;
    --teal: #4cc3dc;
    --violet: #a43fa6;
    --magenta: #b2409c;
    --red: #e8344f;
    --orange: #f4a23a;
    --icon-orange: #ef6a3a;
    --icon-pink: #d8345f;
  }
  * { box-sizing: border-box; margin: 0; padding: 0; }
  html, body { width: 1200px; height: 900px; overflow: hidden; }
  body { background: var(--stage); position: relative; font-family: "Open Sans", sans-serif; }

  .card {
    position: absolute;
    width: 560px;
    height: 320px;
    box-shadow: 0 14px 30px rgba(0,0,0,.45);
    overflow: hidden;
  }

  .brand-dot {
    border-radius: 50%;
    background: linear-gradient(135deg, var(--orange), var(--red) 40%, var(--violet) 70%, var(--teal));
    flex: none;
  }
  .brand-name {
    font-family: "Montserrat", sans-serif;
    font-weight: 700;
    text-transform: uppercase;
    line-height: 1.15;
  }

  /* Product side */
  .card--product {
    left: 60px; top: 110px;
    background: var(--card-dark);
    color: var(--paper-text);
    display: flex; flex-direction: column; align-items: center; justify-content: center;
    text-align: center;
  }
  .product-lockup { display: flex; flex-direction: column; align-items: center; gap: 14px; }
  .product-lockup .brand-dot { width: 56px; height: 56px; }
  .product-lockup .brand-name { font-size: 34px; letter-spacing: 6px; color: var(--paper-text); }
  .tagline { margin-top: 26px; font-size: 17px; letter-spacing: .4px; }
  .product-url { margin-top: 14px; font-size: 14px; letter-spacing: .6px; }
  .product-url b { font-weight: 700; }

  /* Contact side */
  .card--contact {
    left: 580px; top: 470px;
    background: var(--card-light);
    color: var(--ink);
  }
  .contact-lockup { position: absolute; right: 34px; top: 40px; display: flex; align-items: center; gap: 16px; }
  .contact-lockup .brand-dot { width: 40px; height: 40px; }
  .contact-lockup .brand-name { font-size: 26px; letter-spacing: 4px; color: var(--ink); }

  .person { position: absolute; left: 40px; top: 138px; }
  .person__name { font-weight: 700; font-size: 26px; line-height: 1.2; }
  .person__title { font-family: "Questrial", sans-serif; font-size: 14px; letter-spacing: 3px; color: var(--ink-soft); margin-top: 2px; }
  .contact-list { list-style: none; margin-top: 14px; font-size: 14px; color: var(--ink-soft); }
  .contact-list li { display: flex; align-items: center; gap: 10px; margin-bottom: 6px; line-height: 1.3; }
  .contact-list svg { width: 14px; height: 14px; flex: none; }

  .edge-band { position: absolute; left: 0; right: 0; bottom: 0; height: 10px; display: flex; }
  .edge-band__main { flex: 0 0 70%; background: linear-gradient(90deg, var(--teal), var(--magenta) 55%, var(--violet)); }
  .edge-band__gap { flex: 0 0 1%; background: var(--card-light); }
  .edge-band__accent { flex: 1; background: linear-gradient(90deg, var(--red), var(--orange)); }
</style>
</head>
<body>

  <section class="card card--product" aria-label="Product side">
    <div class="product-lockup">
      <span class="brand-dot"></span>
      <span class="brand-name">Glimworld</span>
    </div>
    <p class="tagline">Culturally Immersive Language Learning Games</p>
    <p class="product-url">www.<b>glimworld-play</b>.com</p>
  </section>

  <section class="card card--contact" aria-label="Contact side">
    <div class="contact-lockup">
      <span class="brand-dot"></span>
      <span class="brand-name">Brightloom<br>Language</span>
    </div>

    <div class="person">
      <h1 class="person__name">Nadia Colvert</h1>
      <p class="person__title">CEO</p>
      <ul class="contact-list">
        <li>
          <svg viewBox="0 0 14 14" aria-hidden="true"><path d="M3.2 1.5 5 1.2l1.2 3-1.4 1.1a7 7 0 0 0 3.9 3.9l1.1-1.4 3 1.2-.3 1.8c-.2.8-.9 1.3-1.7 1.2A10 10 0 0 1 1.9 3.2c-.1-.8.4-1.5 1.3-1.7Z" fill="var(--icon-orange)"/></svg>
          (555)-014-2286
        </li>
        <li>
          <svg viewBox="0 0 14 14" aria-hidden="true"><rect x="1" y="3" width="12" height="8" rx="1" fill="none" stroke="var(--icon-orange)" stroke-width="1.6"/><path d="M1.5 3.5 7 8l5.5-4.5" fill="none" stroke="var(--icon-orange)" stroke-width="1.6"/></svg>
          nadia@glimworld-play.com
        </li>
        <li>
          <svg viewBox="0 0 14 14" aria-hidden="true"><circle cx="7" cy="7" r="5.8" fill="none" stroke="var(--icon-pink)" stroke-width="1.3"/><ellipse cx="7" cy="7" rx="2.6" ry="5.8" fill="none" stroke="var(--icon-pink)" stroke-width="1.1"/><path d="M1.2 7h11.6M2 4h10M2 10h10" stroke="var(--icon-pink)" stroke-width="1"/></svg>
          www.glimworld-play.com
        </li>
      </ul>
    </div>

    <div class="edge-band" aria-hidden="true">
      <span class="edge-band__main"></span>
      <span class="edge-band__gap"></span>
      <span class="edge-band__accent"></span>
    </div>
  </section>

</body>
</html>
```